Book cover for book about Climate Change

Looking for a clean, bold, and attractive cover for a mass-market paperback (5.5"x 8.5") about solving the climate change problem. Title is either "Where the Rivers Meet” or A Harbor Made of Glass” (your choice), subtitle is "A practical field guide to mending the weather — so that the young ones after us inherit steady seasons and open skies," author is Lorne Whitcombe. Thinking that it *might* feature an image of Earth (or a portion thereof) and its very thin layer of atmosphere -- but STRONGLY encourage other ideas too!

Requirements
Nice to have
• Keep it positive — NOT scary doom-and-gloom

```html
<!DOCTYPE html>
<html lang="en">
<head>
<meta charset="utf-8">
<title>A Harbor Made of Glass — Lorne Whitcombe</title>
<link href="https://fonts.googleapis.com/css2?family=Josefin+Sans:wght@400;600;700&family=Comfortaa:wght@300;700&display=swap" rel="stylesheet">
<style>
  :root {
    --cover-orange: #ff9214;
    --ink-navy: #17266f;
    --paper-white: #f7f7f7;
    --ocean-deep: #1c3f8a;
    --ocean-mid: #2f6fb0;
    --cloud: #e9eef3;
    --land: #4f8a3a;
  }
  * { margin: 0; padding: 0; box-sizing: border-box; }
  html, body {
    width: 776px;
    height: 1200px;
    overflow: hidden;
    background: var(--cover-orange);
  }
  .cover {
    position: relative;
    width: 776px;
    height: 1200px;
    background: var(--cover-orange);
    overflow: hidden;
  }
  .planet {
    position: absolute;
    left: 0;
    top: 0;
    width: 776px;
    height: 400px;
  }
  .title {
    position: absolute;
    left: 0;
    top: 0;
    font-family: "Josefin Sans", sans-serif;
    font-weight: 700;
    color: var(--paper-white);
    text-transform: uppercase;
    text-shadow: -10px 11px 0 var(--ink-navy);
  }
  .title-line {
    position: absolute;
    left: 75px;
    font-size: 132px;
    line-height: 1;
    white-space: nowrap;
    letter-spacing: -2px;
  }
  .title-line--1 { top: 218px; }
  .title-line--2 { top: 377px; }
  .title-line--3 { top: 536px; }
  .title-line--4 { top: 695px; }
  .subtitle {
    position: absolute;
    left: 78px;
    top: 858px;
    width: 580px;
    font-family: "Comfortaa", sans-serif;
    font-weight: 300;
    font-size: 27px;
    line-height: 45px;
    color: var(--paper-white);
  }
  .subtitle strong { font-weight: 700; }
  .author {
    position: absolute;
    left: 0;
    top: 1112px;
    width: 776px;
    text-align: center;
    font-family: "Josefin Sans", sans-serif;
    font-weight: 600;
    font-size: 30px;
    letter-spacing: 0.55em;
    padding-left: 0.55em;
    color: var(--ink-navy);
    text-transform: uppercase;
    white-space: nowrap;
  }
</style>
</head>
<body>
<main class="cover">
  <svg class="planet" viewBox="0 0 776 400" role="img" aria-label="Photograph of Earth seen from space, blue oceans, swirling white clouds and green land, curving in from the top right corner">
    <defs>
      <radialGradient id="earthTone" cx="0.75" cy="0.1" r="0.9">
        <stop offset="0" stop-color="var(--land)"/>
        <stop offset="0.35" stop-color="var(--ocean-mid)"/>
        <stop offset="0.7" stop-color="var(--ocean-deep)"/>
        <stop offset="1" stop-color="var(--cloud)"/>
      </radialGradient>
    </defs>
    <circle cx="1100" cy="-700" r="1092" fill="url(#earthTone)"/>
  </svg>

  <h1 class="title">
    <span class="title-line title-line--1">A</span>
    <span class="title-line title-line--2">Harbor</span>
    <span class="title-line title-line--3">Made of</span>
    <span class="title-line title-line--4">Glass</span>
  </h1>

  <p class="subtitle">A <strong>practical field guide to mending the weather</strong> — so that the young ones after us inherit steady seasons and open skies.</p>

  <p class="author">Lorne Whitcombe</p>
</main>
</body>
</html>
```